Maple Roster Business Card for recruitment company

We are looking for a Business Card Design that incorporates our personal details and our busines name and logo. We are a specialized search consultancy that recruit Property and Construction professionals.
We would like a business card that stands out and is appealing to the Construction and Property industry as well.

Target Market(s)

people in the construction and property industry

Contact Information for Business Card

Business Name and logo

Font styles to use
Serif

Colors
0094D4
00A9DD
6FCCEA
C7EBF8
E9F6FB

Requirements
Must have
• Business name and logo as well as contact details
Should not have
• No photos of us please

```html
<!DOCTYPE html>
<html lang="en">
<head>
<meta charset="utf-8">
<title>Maple Roster – Business Card</title>
<link rel="stylesheet" href="https://fonts.googleapis.com/css2?family=Mulish:wght@700&family=Questrial&display=swap">
<style>
  :root {
    --backdrop: #2b2d2e;
    --card-white: #ffffff;
    --card-white-edge: #efefef;
    --navy: #0b3a52;
    --navy-deep: #032c42;
    --navy-light: #0a4862;
    --ink: #3a3a3a;
    --on-dark: #ffffff;
  }
  * { margin: 0; padding: 0; box-sizing: border-box; }
  html, body { width: 1200px; height: 732px; overflow: hidden; }
  body {
    background: var(--backdrop);
    position: relative;
    font-family: "Questrial", "Century Gothic", sans-serif;
  }
  .card {
    position: absolute;
    top: 242px;
    width: 436px;
    height: 249px;
    box-shadow: 0 8px 18px rgba(0,0,0,0.45);
  }
  .card--front {
    left: 144px;
    background: linear-gradient(160deg, var(--card-white) 40%, var(--card-white-edge));
    color: var(--ink);
  }
  .card--back { left: 621px; overflow: hidden; }

  .wordmark {
    position: absolute;
    top: 14px;
    left: 0; right: 0;
    text-align: center;
    font-size: 36px;
    letter-spacing: 1px;
    color: var(--navy);
    text-transform: uppercase;
    line-height: 40px;
  }
  .identity {
    position: absolute;
    right: 200px;
    top: 112px;
    text-align: right;
    white-space: nowrap;
  }
  .identity__name {
    font-family: "Mulish", "Century Gothic", sans-serif;
    font-weight: 700;
    font-size: 17px;
    color: var(--navy);
    line-height: 22px;
  }
  .identity__role { font-size: 12.5px; line-height: 16px; }
  .divider-v {
    position: absolute;
    left: 244px; top: 112px;
    width: 1px; height: 38px;
    background: var(--navy);
  }
  .contact {
    position: absolute;
    left: 254px; top: 110px;
    list-style: none;
    font-size: 12.5px;
    line-height: 14.5px;
    white-space: nowrap;
  }
  .contact__label {
    display: inline-block;
    width: 19px;
    font-family: "Mulish", sans-serif;
    font-weight: 700;
    color: var(--navy);
    font-size: 11.5px;
  }
  .divider-h {
    position: absolute;
    left: 108px; top: 202px;
    width: 223px; height: 1px;
    background: var(--navy);
  }
  .location {
    position: absolute;
    left: 0; right: 0; top: 216px;
    text-align: center;
    font-size: 12.5px;
  }

  .back__pattern {
    position: absolute; inset: 0;
    background: radial-gradient(circle at 30% 20%, var(--navy-light), var(--navy-deep) 75%);
  }
  .back__name {
    position: absolute;
    left: 0; right: 0; top: 110px;
    text-align: center;
    font-size: 24px;
    color: var(--on-dark);
    letter-spacing: 1px;
  }
</style>
</head>
<body>
  <section class="card card--front" aria-label="Business card front">
    <div class="wordmark">Maple Roster</div>
    <div class="identity">
      <div class="identity__name">Claire Whitfield</div>
      <div class="identity__role">Director&nbsp; | &nbsp;Senior Search Consultant</div>
    </div>
    <div class="divider-v"></div>
    <ul class="contact">
      <li><span class="contact__label">T:</span> +64 27 555 0142</li>
      <li><span class="contact__label">E:</span> claire@mapleroster.nz</li>
      <li><span class="contact__label">W:</span>www.mapleroster.nz</li>
    </ul>
    <div class="divider-h"></div>
    <div class="location">Auckland, New Zealand</div>
  </section>

  <section class="card card--back" aria-label="Business card back">
    <div class="back__pattern" role="img" aria-label="Deep navy background with a faint repeating brand-symbol pattern"></div>
    <div class="back__name">Maple Roster</div>
  </section>
</body>
</html>
```